Profesional personal website needs design and business card

I need a business card with my professional name as a logo "Dorian Vitality" for my business. I am a Wellness Coach, consultant and trainer. So it should be professional, wellness oriented and modern.

Target Market(s)

Private clients, governments, corporations. Luxury and high market.

Industry/Entity Type

Health And Wellness

Contact Information for Business Card

Dorian Vitality should be the logo

Colors

Designer to choose colors to be used in the design.

Requirements
Must have
• Dorian Vitality
• Name: Tomás Lirandel
• Wellness Coach, Consultant & Trainer.
• Website: www.dorianvitality-example.com
• Phone:
• Spain (+34) 612 480 317
• (USA) +1 (555) 610 4829
Nice to have
• The most important is the design of "Dorian Vitality", as this is going to be my personal brand logo. It should be professional, wellness, high end and actual.
Should not have
• no golds, no baroque style..

```html
<!DOCTYPE html>
<html lang="en">
<head>
<meta charset="utf-8">
<title>Dorian Vitality — Business Card</title>
<link href="https://fonts.googleapis.com/css2?family=Lato:ital,wght@0,400;0,700;0,900;1,400&display=swap" rel="stylesheet">
<style>
  :root {
    --brand-blue: #1177c2;
    --ink-grey: #5f6164;
    --band-grey: #77797c;
    --paper: #ffffff;
    --stage: #2a2a2a;
  }
  * { box-sizing: border-box; margin: 0; padding: 0; }
  html, body { width: 1200px; height: 878px; overflow: hidden; }
  body {
    background: var(--stage);
    font-family: "Lato", Arial, sans-serif;
    display: flex;
    flex-direction: column;
    align-items: center;
    justify-content: center;
    gap: 44px;
  }
  .card {
    width: 660px;
    height: 377px;
    position: relative;
    overflow: hidden;
  }

  /* Front */
  .card-front {
    background: var(--brand-blue);
    color: var(--paper);
    display: flex;
    flex-direction: column;
    align-items: center;
    justify-content: center;
  }
  .front-wordmark {
    display: flex;
    align-items: center;
    gap: 16px;
    font-weight: 900;
    font-size: 46px;
    letter-spacing: 1px;
    text-transform: uppercase;
  }
  .front-wordmark .mark-dot {
    width: 22px; height: 22px; border-radius: 50%;
    background: var(--paper);
  }
  .front-url {
    margin-top: 26px;
    font-size: 15px;
    letter-spacing: 5px;
  }

  /* Back */
  .card-back { background: var(--paper); }
  .holder {
    position: absolute; left: 40px; top: 34px;
  }
  .holder-name {
    color: var(--brand-blue);
    font-weight: 900;
    font-size: 31px;
    letter-spacing: 0.5px;
    text-transform: uppercase;
  }
  .holder-role {
    color: var(--ink-grey);
    font-size: 17px;
    margin-top: 2px;
  }
  .contacts {
    position: absolute; left: 40px; bottom: 52px;
    list-style: none;
    color: var(--ink-grey);
    font-size: 19px;
    line-height: 29px;
  }
  .contacts li { display: flex; align-items: center; gap: 14px; }
  .contacts svg { width: 18px; height: 18px; flex: none; }
  .contacts .url-core { color: var(--brand-blue); }
  .back-wordmark {
    position: absolute; right: 40px; top: 168px;
    display: flex; align-items: center; gap: 12px;
    color: var(--brand-blue);
    font-weight: 900;
    font-size: 30px;
    letter-spacing: 0.5px;
    text-transform: uppercase;
  }
  .back-wordmark .mark-dot {
    width: 16px; height: 16px; border-radius: 50%;
    background: var(--brand-blue);
  }
  .band {
    position: absolute; left: 0; right: 0; bottom: 0; height: 20px;
    background: var(--brand-blue);
  }
  .band-tab {
    position: absolute; left: 0; bottom: 20px;
    width: 52px; height: 22px;
    background: var(--band-grey);
  }
</style>
</head>
<body>

  <section class="card card-front" aria-label="Card front">
    <div class="front-wordmark"><span class="mark-dot"></span>Dorian Vitality</div>
    <div class="front-url">www.dorianvitality-example.com</div>
  </section>

  <section class="card card-back" aria-label="Card back">
    <div class="holder">
      <h1 class="holder-name">Tomás Lirandel</h1>
      <p class="holder-role">Wellness Coach, Consultant &amp; Trainer</p>
    </div>

    <div class="back-wordmark"><span class="mark-dot"></span>Dorian Vitality</div>

    <ul class="contacts">
      <li>
        <svg viewBox="0 0 24 24" aria-hidden="true"><path fill="#1177c2" d="M6.6 10.8a15 15 0 0 0 6.6 6.6l2.2-2.2a1 1 0 0 1 1-.25 11.4 11.4 0 0 0 3.6.57 1 1 0 0 1 1 1V20a1 1 0 0 1-1 1A17 17 0 0 1 3 4a1 1 0 0 1 1-1h3.5a1 1 0 0 1 1 1c0 1.25.2 2.45.57 3.6a1 1 0 0 1-.25 1z"/></svg>
        (+34) 612 480 317 (Spain)
      </li>
      <li>
        <svg viewBox="0 0 24 24" aria-hidden="true"><path fill="#1177c2" d="M6.6 10.8a15 15 0 0 0 6.6 6.6l2.2-2.2a1 1 0 0 1 1-.25 11.4 11.4 0 0 0 3.6.57 1 1 0 0 1 1 1V20a1 1 0 0 1-1 1A17 17 0 0 1 3 4a1 1 0 0 1 1-1h3.5a1 1 0 0 1 1 1c0 1.25.2 2.45.57 3.6a1 1 0 0 1-.25 1z"/></svg>
        +1 (555) 610 4829 (USA)
      </li>
      <li>
        <svg viewBox="0 0 24 24" aria-hidden="true"><rect x="2" y="5" width="20" height="14" fill="#1177c2"/><path d="M2 5l10 8 10-8" fill="none" stroke="#fff" stroke-width="1.6"/></svg>
        info@dorianvitality-example.com
      </li>
      <li>
        <svg viewBox="0 0 24 24" aria-hidden="true"><circle cx="12" cy="12" r="9.5" fill="none" stroke="#1177c2" stroke-width="1.8"/><ellipse cx="12" cy="12" rx="4" ry="9.5" fill="none" stroke="#1177c2" stroke-width="1.4"/><path d="M2.5 12h19M4.5 7h15M4.5 17h15" stroke="#1177c2" stroke-width="1.4"/></svg>
        <span>www.<span class="url-core">dorianvitality-example</span>.com</span>
      </li>
    </ul>

    <div class="band-tab"></div>
    <div class="band"></div>
  </section>

</body>
</html>
```